Business Performance Improvement Book Cover Design Project

We need a book cover design for a new company, based in Eastern Australia, called Brovanta Consulting. We advise clients on process improvement, continuous improvement and business performance improvement, especially in the manufacturing areas and Fast Moving Consumer Goods industries.
We have a written a book designed to demonstrate our very high calibre of knowledge and to use as a marketing tool for prospective clients. We hope to give it out at training seminars and as a comprehensive business card.

Title of the book is: A rounded method for Enterprise Results Advancement.
Subtitle: Shape a Steady Refinement method to fit your firm's character.
Author: by Gareth Polwyn
Back Cover: No need for a bar code in this edition. An important aspect is that we will distribute by hand. Text below for back page.

'For the experienced Business Performers, this book is designed to offer an insight into the advantages and an example of an approach to Business Improvement. It is not the only way but it is tried and tested in world class companies and it works. For those new to Continuous Improvement, it offers a helpful introduction to a holistic business improvement system, an overview of important success factors and pitfalls, recommendations on how to implement tools and methods and a quick guide to see when to use which tools. '

'Consultancies are one of many tools management teams can engage and management must make sure the consultants tailor their approach to suit its business needs and culture and not vice versa.'

End of text for back cover.

Business Performance Improvement is also known as or can include:
Continuous Improvement
Process Improvement
Lean Six Sigma
Operational Excellence
Total Productive Maintenance
Varmeco Output Method
Total Quality Management
Business Process Re engineering
Yield Compass
=
Brovanta Consulting

The book size is 175 x 240 mm and will need a 10-15mm bleed. The spine is not known at this stage exactly and will need to be updated once the printing is finished but I suggest a 10mm until I have the exact size.

Our company colours are Pantone 288, R0,G75,B141, C100,M79,Y17,K3. Attached are some other publications that give a sense of what we like to portray, Some words which might add to this are: professional, elegance, quality, sleek.
Updates

Reason: After receiving the designs, I realised that I needed to update the brief with more and better quality information for designers to work with.

Target Market(s)

people in the accounting and insolvency industries, production managers and CEOs, Chief Operating Officers, members of the executive team of large companies and GMs of small companies.

Industry/Entity Type

Marketing

Requirements
Must have
• Communicate an image that shows an improvement or increase of something.
Very professional and elegant
Emphasis on the words 'Business Performance Improvement' in the title, subtitle also important
Must appeal to a high-end of the market audience
Nice to have
• Recommendation for your cover to be gloss or matt in print
Image can be indirectly related to money but not specifically
Somehow that it matches or is not so different to the attached brochure
Should not have
• Not be too loud or commercial
Book jacket. WIll be printed as soft cover first run and hard cover 2nd run

```html
<!DOCTYPE html>
<html lang="en">
<head>
<meta charset="utf-8">
<title>A Rounded Method for Enterprise Results Advancement — Book Cover</title>
<link rel="stylesheet" href="https://fonts.googleapis.com/css2?family=Noto+Serif:wdth,wght@62.5..100,400&display=swap">
<style>
  :root {
    --paper: #ffffff;
    --ink: #0b0b0b;
    --ink-shadow: rgba(0, 0, 0, 0.55);
    --ornament-light: #5d82aa;
    --ornament-mid: #45698f;
    --ornament-dark: #2f4f73;
  }
  html, body {
    margin: 0;
    padding: 0;
    overflow: hidden;
    background: var(--paper);
  }
  .cover {
    position: relative;
    width: 846px;
    height: 1200px;
    background: var(--paper);
    overflow: hidden;
    font-family: "Noto Serif", Georgia, serif;
    font-stretch: 87.5%;
    color: var(--ink);
  }
  .ornament {
    position: absolute;
    background: radial-gradient(ellipse at 35% 40%, var(--ornament-light), var(--ornament-mid) 55%, var(--ornament-dark));
    opacity: 0.9;
  }
  .ornament--top {
    left: 0;
    top: 0;
    width: 370px;
    height: 470px;
    border-radius: 0 60% 55% 0 / 0 45% 60% 0;
  }
  .ornament--bottom {
    left: 0;
    top: 625px;
    width: 340px;
    height: 575px;
    border-radius: 0 55% 0 0 / 0 40% 0 0;
  }
  .title {
    position: absolute;
    right: 44px;
    top: 58px;
    margin: 0;
    text-align: right;
    font-weight: 400;
    font-size: 76px;
    line-height: 106px;
    letter-spacing: -0.5px;
    text-shadow: 4px 4px 4px var(--ink-shadow);
  }
  .title span { display: block; }
  .subtitle {
    position: absolute;
    right: 46px;
    top: 592px;
    margin: 0;
    text-align: right;
    font-size: 35px;
    line-height: 45px;
    text-shadow: 3px 3px 3px var(--ink-shadow);
  }
  .subtitle span { display: block; }
  .author {
    position: absolute;
    right: 46px;
    top: 1102px;
    margin: 0;
    font-size: 31px;
    line-height: 40px;
    text-shadow: 3px 3px 3px var(--ink-shadow);
    white-space: nowrap;
  }
</style>
</head>
<body>
  <main class="cover">
    <div class="ornament ornament--top" role="img" aria-label="Blue embossed floral swirl ornament in the top-left corner"></div>
    <div class="ornament ornament--bottom" role="img" aria-label="Blue embossed floral swirl and leaf ornament along the lower-left edge"></div>

    <h1 class="title">
      <span>A Rounded</span>
      <span>Method</span>
      <span>For Enterprise</span>
      <span>Results</span>
      <span>Advancement</span>
    </h1>

    <p class="subtitle">
      <span>Shape a</span>
      <span>Steady Refinement</span>
      <span>method to fit your firm's</span>
      <span>character.</span>
    </p>

    <p class="author">Gareth Polwyn B. Mech Eng., M. Sc (KVT)</p>
  </main>
</body>
</html>
```